Visitenkarten-Design für Boutique-Unternehmensberatung
Zielgruppe
Boutique Unternehmensberatung für die Chemische Industrie. Wir unterstützen Unternehmen, die Beziehung zu Ihren Händlern zu optimieren.
Vorläufige Website vertriebsbruecke-online.de kann ggf weitere Einblicke geben. Hinweis: Diese Website wurde bisher noch nicht professionell erstellt.
Aufgabenstellung
Die Visitenkarte sollte vertrauenserweckend und seriös wirken. Zeitgleich aber auch modern.

```html
<!DOCTYPE html>
<html lang="de">
<head>
<meta charset="utf-8">
<title>Visitenkarte Vertriebsbrücke</title>
<link href="https://fonts.googleapis.com/css2?family=Montserrat:wght@400;500;700;800&display=swap" rel="stylesheet">
<style>
  :root {
    --brand-blue: #0f5592;
    --paper: #ffffff;
    --backdrop: #b9bcc1;
    --photo-light: #c9d3dc;
    --photo-dark: #8a96a3;
  }
  * { box-sizing: border-box; margin: 0; padding: 0; }
  html, body { width: 1200px; height: 852px; overflow: hidden; }
  body {
    background: var(--backdrop);
    font-family: "Montserrat", Arial, sans-serif;
    position: relative;
  }
  .card {
    position: absolute;
    top: 251px;
    width: 540px;
    height: 349px;
    overflow: hidden;
  }
  .card--front { left: 40px; background: var(--brand-blue); }
  .card--back { left: 620px; background: var(--paper); }

  .brand {
    display: flex;
    align-items: center;
    gap: 12px;
    font-weight: 700;
  }
  .brand__dot { border-radius: 50%; flex: none; }
  .card--front .brand {
    position: absolute;
    left: 50%; top: 50%;
    transform: translate(-50%, -50%);
    color: var(--paper);
    font-size: 30px;
  }
  .card--front .brand__dot { width: 34px; height: 34px; background: var(--paper); }

  .header-band { position: absolute; left: 0; top: 0; }
  .person {
    position: absolute;
    left: 30px; top: 62px;
    color: var(--paper);
  }
  .person__name { font-weight: 800; font-size: 27px; letter-spacing: 0.3px; }
  .person__role { font-weight: 400; font-size: 16px; margin-left: 6px; }
  .person__contacts {
    display: flex;
    gap: 22px;
    margin-top: 12px;
    font-size: 11px;
  }
  .contact { display: flex; align-items: center; gap: 6px; }
  .icon { width: 13px; height: 13px; flex: none; }

  .portrait {
    position: absolute;
    left: 222px; top: 172px;
    width: 90px; height: 90px;
    border-radius: 50%;
    border: 5px solid var(--paper);
    background: radial-gradient(circle at 45% 40%, var(--photo-light), var(--photo-dark));
  }

  .company {
    position: absolute;
    left: 348px; top: 184px;
    color: var(--brand-blue);
    font-size: 9.5px;
    line-height: 1.55;
    white-space: nowrap;
  }
  .company__name { font-weight: 700; font-size: 10.5px; }
  .company__address { margin-top: 6px; }
  .company__contacts { margin-top: 10px; list-style: none; }
  .company__contacts .contact { gap: 5px; }

  .card--back .brand {
    position: absolute;
    left: 36px; bottom: 34px;
    color: var(--brand-blue);
    font-size: 17px;
    gap: 8px;
  }
  .card--back .brand__dot { width: 18px; height: 18px; background: var(--brand-blue); }
</style>
</head>
<body>

<section class="card card--front">
  <div class="brand"><span class="brand__dot"></span><span class="brand__name">Vertriebsbrücke</span></div>
</section>

<section class="card card--back">
  <svg class="header-band" width="540" height="349" viewBox="0 0 540 349" aria-hidden="true">
    <path d="M0 0 H470 C458 130 360 205 0 238 Z" fill="var(--brand-blue)"/>
  </svg>

  <div class="person">
    <p><span class="person__name">Jonas Brandt</span><span class="person__role">• Geschäftsführer / CEO</span></p>
    <div class="person__contacts">
      <span class="contact">
        <svg class="icon" viewBox="0 0 16 16" aria-hidden="true"><circle cx="8" cy="8" r="8" fill="#fff"/><path d="M5.2 4.2l1.4-.3.8 2-1 .7a5 5 0 0 0 2.9 2.9l.7-1 2 .8-.3 1.4c-3.6.4-7-3-6.5-6.5z" fill="var(--brand-blue)"/></svg>
        +49 6150 / 12 34 56 70
      </span>
      <span class="contact">
        <svg class="icon" viewBox="0 0 16 16" aria-hidden="true"><circle cx="8" cy="8" r="8" fill="#fff"/><rect x="4" y="5" width="8" height="6" rx="1" fill="var(--brand-blue)"/><path d="M4.3 5.4L8 8.3l3.7-2.9" stroke="#fff" stroke-width="0.9" fill="none"/></svg>
        jb@vertriebsbruecke-online.de
      </span>
    </div>
  </div>

  <div class="portrait" role="img" aria-label="Porträtfoto von Jonas Brandt"></div>

  <div class="company">
    <p class="company__name">JBR Vertriebsbrücke<br>GmbH i.G.</p>
    <p class="company__address">Lindenallee 12<br>64289 Musterstadt</p>
    <ul class="company__contacts">
      <li class="contact">
        <svg class="icon" viewBox="0 0 16 16" aria-hidden="true"><circle cx="8" cy="8" r="8" fill="var(--brand-blue)"/><path d="M5.2 4.2l1.4-.3.8 2-1 .7a5 5 0 0 0 2.9 2.9l.7-1 2 .8-.3 1.4c-3.6.4-7-3-6.5-6.5z" fill="#fff"/></svg>
        +49 6150 / 12 34 56 70
      </li>
      <li class="contact">
        <svg class="icon" viewBox="0 0 16 16" aria-hidden="true"><circle cx="8" cy="8" r="8" fill="var(--brand-blue)"/><rect x="4" y="5" width="8" height="6" rx="1" fill="#fff"/><path d="M4.3 5.4L8 8.3l3.7-2.9" stroke="var(--brand-blue)" stroke-width="0.9" fill="none"/></svg>
        info@vertriebsbruecke-online.de
      </li>
      <li class="contact">
        <svg class="icon" viewBox="0 0 16 16" aria-hidden="true"><circle cx="8" cy="8" r="8" fill="var(--brand-blue)"/><circle cx="8" cy="8" r="4" stroke="#fff" stroke-width="0.9" fill="none"/><path d="M4 8h8M8 4c-2 2.4-2 5.6 0 8M8 4c2 2.4 2 5.6 0 8" stroke="#fff" stroke-width="0.8" fill="none"/></svg>
        www.vertriebsbruecke-online.de
      </li>
    </ul>
  </div>

  <div class="brand"><span class="brand__dot"></span><span class="brand__name">Vertriebsbrücke</span></div>
</section>

</body>
</html>
```